The Linen Loft Co

We need a business card design for our wardrobe company.
Please visit our website www.gentlelinenlofts.com to get an idea of who we are.

```html
<!DOCTYPE html>
<html lang="en">
<head>
<meta charset="utf-8">
<title>The Linen Loft Co — Business Card</title>
<link rel="stylesheet" href="https://fonts.googleapis.com/css2?family=Roboto:wght@300;400;500&display=swap">
<style>
  :root {
    --backdrop: #6e6964;
    --card-white: #f4f4f4;
    --card-white-edge: #ebebeb;
    --tan: #c8b496;
    --tan-text: #b9a283;
    --ink: #111111;
    --grey-text: #5e5e5e;
    --muted: #8c8c8c;
    --icon: #c2ad8f;
    --back-dark: #0c0b0a;
    --back-glow: #2b2620;
    --back-gold: #d2bd9c;
  }
  * { margin: 0; padding: 0; box-sizing: border-box; }
  html, body {
    width: 1125px; height: 1200px; overflow: hidden;
    background: var(--backdrop);
    font-family: "Roboto", Arial, sans-serif;
  }
  .canvas { position: relative; width: 1125px; height: 1200px; }

  .card {
    position: absolute; left: 162px; width: 800px; height: 455px;
    box-shadow: 0 4px 10px rgba(0,0,0,0.35);
  }
  .card-front { top: 95px; background: linear-gradient(90deg, var(--card-white), var(--card-white-edge)); }
  .card-back {
    top: 612px;
    background: radial-gradient(ellipse at 50% 45%, var(--back-glow) 0%, var(--back-dark) 70%);
  }

  .front-band { position: absolute; left: 0; top: 0; width: 223px; height: 100%; background: var(--tan); }

  .brand-mark { position: absolute; width: 22px; height: 22px; }
  .brand-name { position: absolute; font-weight: 500; letter-spacing: 0.2px; white-space: nowrap; }
  .brand-tagline { position: absolute; font-weight: 500; white-space: nowrap; }

  .card-front .brand-mark { left: 192px; top: 190px; background: var(--ink); }
  .card-front .brand-name { left: 227px; top: 186px; font-size: 23px; color: var(--ink); }
  .card-front .brand-tagline { left: 254px; top: 225px; font-size: 20px; color: var(--ink); }

  .person { position: absolute; right: 53px; top: 62px; text-align: right; }
  .person-name { font-size: 31px; font-weight: 400; color: var(--tan-text); line-height: 1.1; }
  .person-title { font-size: 20px; font-weight: 400; color: var(--muted); line-height: 1.25; }

  .address {
    position: absolute; right: 53px; top: 282px; text-align: right;
    font-size: 19px; color: var(--grey-text); line-height: 24px;
  }
  .contacts {
    position: absolute; right: 49px; top: 341px; list-style: none;
    font-size: 19px; color: var(--grey-text); line-height: 24px;
  }
  .contacts li { display: flex; justify-content: flex-end; align-items: center; gap: 13px; }
  .contacts svg { width: 17px; height: 17px; fill: var(--icon); }

  .card-back .brand-mark { left: 310px; top: 222px; background: var(--back-gold); }
  .card-back .brand-name { left: 347px; top: 217px; font-size: 25px; color: var(--back-gold); }
  .card-back .brand-tagline { left: 375px; top: 256px; font-size: 21px; color: var(--back-gold); }
</style>
</head>
<body>
<main class="canvas">
  <section class="card card-front" aria-label="Business card front">
    <div class="front-band"></div>
    <span class="brand-mark"></span>
    <p class="brand-name">THE LINEN LOFT CO</p>
    <p class="brand-tagline">Built to Fit Every Room</p>

    <div class="person">
      <p class="person-name">Daniel Hartley</p>
      <p class="person-title">President</p>
    </div>

    <p class="address">Norland House, 42 Mill Lane,<br>London N4 7QT</p>

    <ul class="contacts">
      <li>020 7946 0321
        <svg viewBox="0 0 24 24" aria-hidden="true"><path d="M6.6 10.8a15.1 15.1 0 0 0 6.6 6.6l2.2-2.2c.3-.3.7-.4 1-.2 1.1.4 2.3.6 3.6.6.6 0 1 .4 1 1V20c0 .6-.4 1-1 1A17 17 0 0 1 3 4c0-.6.4-1 1-1h3.5c.6 0 1 .4 1 1 0 1.3.2 2.5.6 3.6.1.3 0 .7-.2 1z"/></svg>
      </li>
      <li>info@gentlelinenlofts.com
        <svg viewBox="0 0 24 24" aria-hidden="true"><path d="M2 5h20v1.5l-10 6-10-6z"/><path d="M2 8.5l10 6 10-6V19H2z"/></svg>
      </li>
      <li>www.gentlelinenlofts.com
        <svg viewBox="0 0 24 24" aria-hidden="true"><circle cx="12" cy="12" r="10"/><path d="M7 6c2 1 3 3 2 5s-3 1-3 4 M14 4c-1 2 1 3 3 3s2 3 1 5-3 2-3 5" fill="none" stroke="#f0f0f0" stroke-width="1.6"/></svg>
      </li>
    </ul>
  </section>

  <section class="card card-back" aria-label="Business card back">
    <span class="brand-mark"></span>
    <p class="brand-name">THE LINEN LOFT CO</p>
    <p class="brand-tagline">Built to Fit Every Room</p>
  </section>
</main>
</body>
</html>
```